Business card for a Exhibition booth fabrication company

Hi. My company would like to change our corporate name card. We are an events and Exhibition stand builder company. We would like our corporate name card to resonate what we do. I need someone to create something unique that relates to the industry that I am in. The graphic designer should be creative to incorporate the elements of my industry and try to blend in well in the design of the card. Our aim is to ensure that we are unique and our card can look different from our competitors.
Updates

Target Market(s)

Marketing and events manager from all companies

Contact Information for Business Card

The business card should have the following details:
Name
Job Title
Email
Website

Colors

Designer to choose colors to be used in the design.

Requirements
Must have
• The card must be look something that is relevant to the service that I am providing. My website is: www.velmora-buildworks.com
• You can see my website to get more information on what service that I am doing
Nice to have
• On the back of my card, I would like to have a globe image with the incorporation of my company logo. This is to indicate that my services can be done in any part of the world.

```html
<!DOCTYPE html>
<html lang="en">
<head>
<meta charset="UTF-8">
<title>Velmora Buildworks – Business Card</title>
<link href="https://fonts.googleapis.com/css2?family=Montserrat:wght@400;600;700&family=Open+Sans:wght@400;600&display=swap" rel="stylesheet">
<style>
  :root {
    --backdrop: #e6e6e6;
    --card: #ffffff;
    --brand-red: #e41b23;
    --band-grey: #5f5f61;
    --brand-grey: #6e6e70;
    --ink: #222222;
    --title-grey: #d8d8d8;
    --map-light: #f1f1f1;
    --map-mid: #d6d6d6;
  }
  * { margin: 0; padding: 0; box-sizing: border-box; }
  html, body { width: 1200px; height: 960px; overflow: hidden; }
  body {
    background: var(--backdrop);
    position: relative;
    font-family: "Open Sans", Arial, sans-serif;
  }
  .card {
    position: absolute;
    left: 220px;
    width: 760px;
    height: 434px;
    background: var(--card);
    overflow: hidden;
    box-shadow: 0 6px 18px rgba(0,0,0,0.12);
  }
  .card--front { top: 30px; }
  .card--back { top: 496px; }

  .brand {
    position: absolute;
    display: flex;
    align-items: center;
    gap: 14px;
  }
  .brand__dot {
    width: 30px; height: 30px;
    border-radius: 50%;
    background: var(--brand-red);
    flex: none;
  }
  .brand__name {
    font-family: "Montserrat", Arial, sans-serif;
    font-weight: 600;
    color: var(--brand-grey);
    letter-spacing: 3px;
    white-space: nowrap;
  }
  .card--front .brand { left: 60px; top: 58px; }
  .card--front .brand__name { font-size: 26px; }

  .name-band {
    position: absolute;
    left: 0; top: 150px;
    width: 440px; height: 82px;
    background: var(--band-grey);
    padding: 12px 0 0 44px;
  }
  .name-band__name {
    font-family: "Montserrat", Arial, sans-serif;
    font-weight: 700;
    font-size: 27px;
    color: #ffffff;
    letter-spacing: 1px;
  }
  .name-band__title {
    font-family: "Montserrat", Arial, sans-serif;
    font-weight: 400;
    font-size: 16px;
    color: var(--title-grey);
    letter-spacing: 1px;
  }

  .contact-icons {
    position: absolute;
    left: 400px; top: 232px;
    width: 40px; height: 88px;
    background: var(--band-grey);
    display: flex;
    flex-direction: column;
    justify-content: space-around;
    align-items: center;
    padding: 6px 0;
  }
  .contact-band {
    position: absolute;
    left: 440px; top: 232px;
    width: 320px; height: 120px;
    background: var(--brand-red);
    padding: 12px 0 0 16px;
    color: #ffffff;
    font-size: 18px;
    line-height: 27px;
  }

  .address {
    position: absolute;
    left: 30px; top: 262px;
    display: flex;
    align-items: center;
    gap: 8px;
    font-size: 15px;
    color: var(--ink);
  }

  .world-map-area {
    position: absolute;
    left: 110px; top: 34px;
    width: 600px; height: 240px;
    border-radius: 6px;
    background: linear-gradient(180deg, var(--map-light) 0%, var(--map-mid) 100%);
  }
  .card--back .brand {
    left: 0; right: 0; top: 306px;
    justify-content: center;
  }
  .card--back .brand__name { font-size: 34px; }
</style>
</head>
<body>

  <section class="card card--front" aria-label="Business card front">
    <div class="brand">
      <span class="brand__dot"></span>
      <span class="brand__name">VELMORA BUILDWORKS</span>
    </div>

    <div class="name-band">
      <p class="name-band__name">DANIEL OKAFOR</p>
      <p class="name-band__title">PRESIDENT</p>
    </div>

    <div class="address">
      <svg width="16" height="16" viewBox="0 0 16 16" aria-hidden="true">
        <circle cx="8" cy="8" r="7" fill="none" stroke="var(--brand-red)" stroke-width="1.5"/>
        <path d="M8 3.5a3 3 0 0 0-3 3c0 2.2 3 5.5 3 5.5s3-3.3 3-5.5a3 3 0 0 0-3-3z" fill="var(--brand-red)"/>
      </svg>
      <span>Street Name, City Name, Zipcode - 01234</span>
    </div>

    <div class="contact-icons" aria-hidden="true">
      <svg width="16" height="16" viewBox="0 0 16 16">
        <path d="M4 1.5l2.2 2.6-1.3 1.7c.9 2 2.4 3.5 4.4 4.4l1.7-1.3 2.6 2.2-1.4 2.4C7 13 3 9 1.5 4z" fill="#ffffff"/>
      </svg>
      <svg width="18" height="14" viewBox="0 0 18 14">
        <rect x="1" y="1" width="16" height="12" fill="none" stroke="#ffffff" stroke-width="1.6"/>
        <polyline points="1,1 9,8 17,1" fill="none" stroke="#ffffff" stroke-width="1.6"/>
      </svg>
      <svg width="18" height="18" viewBox="0 0 18 18">
        <circle cx="9" cy="9" r="7.5" fill="none" stroke="#ffffff" stroke-width="1.4"/>
        <ellipse cx="9" cy="9" rx="3.2" ry="7.5" fill="none" stroke="#ffffff" stroke-width="1.2"/>
        <line x1="1.5" y1="9" x2="16.5" y2="9" stroke="#ffffff" stroke-width="1.2"/>
      </svg>
    </div>
    <div class="contact-band">
      <p>012-555-0148</p>
      <p>info@velmora-buildworks.com</p>
      <p>www.velmora-buildworks.com</p>
    </div>
  </section>

  <section class="card card--back" aria-label="Business card back">
    <div class="world-map-area" role="img" aria-label="Light grey world map showing global reach"></div>
    <div class="brand">
      <span class="brand__dot"></span>
      <span class="brand__name">VELMORA BUILDWORKS</span>
    </div>
  </section>

</body>
</html>
```